Stickers By Dwayne needs a website and logo design

I am starting a home business, "Stickers By Dwayne", which I will sell car decals/decals of some sort. I am looking for a creative and professional looking website. I do not want anything too plain/bland, or else I could design it myself. I am up for many options, when it comes to text/colors, and I am not opposed to much. Just nothing too plain. Currently have no logo design to use, may also add this to the project as well. ( I use Wordpress for my site server so it has to be compatible to be used with that website.
Also, I make decals that mainly go on car windows, not as big on car body’s. Also put decals on glassware, and other items. But mainly car windows

• some color, not be bland and white everywhere.

```html
<!DOCTYPE html>
<html lang="en">
<head>
<meta charset="utf-8">
<title>Stickers By Dwayne</title>
<link rel="stylesheet" href="https://fonts.googleapis.com/css2?family=Lato:ital,wght@0,400;0,700;0,900;1,400&display=swap">
<style>
:root{
  --navy:#1e3f9c;
  --pink:#e0287a;
  --teal:#1aa3b8;
  --green:#4fa83a;
  --ink:#2b2b2b;
  --cyan-soft:#7fdcf0;
  --pink-soft:#f1a9d4;
  --yellow-soft:#e4d66e;
  --cyan-bright:#16dbea;
  --footer:#111214;
  --white:#ffffff;
}
*{margin:0;padding:0;box-sizing:border-box}
html,body{width:1200px;height:3191px;overflow:hidden}
body{position:relative;font-family:'Lato',sans-serif;color:var(--ink);background:var(--white)}
.band{position:absolute;left:0;width:1200px}
.abs{position:absolute}

/* header */
.site-header{top:0;height:96px;background:var(--white);z-index:20}
.brand{left:74px;top:24px;font-weight:900;font-size:26px;line-height:26px;color:var(--ink);letter-spacing:1px;text-transform:uppercase}
.brand small{display:block;font-size:17px;line-height:22px;letter-spacing:.5px;padding-left:70px}
.topbar{right:60px;top:24px;display:flex;gap:26px;align-items:center;font-size:15px;font-weight:700}
.topbar .phone{color:var(--green)}
.topbar .ship{color:var(--teal)}
.topbar .ship b{color:var(--pink)}
.topbar .cart{color:var(--navy)}
.topbar svg{vertical-align:-2px;margin-right:6px}
.main-nav{right:56px;top:72px;display:flex;gap:40px;font-size:12.5px;font-weight:700;letter-spacing:.4px}
.main-nav a{color:var(--ink);text-decoration:none}
.main-nav a.active{color:var(--pink)}

/* hero */
.hero{top:96px;height:604px;background:linear-gradient(160deg,#3b4046 0%,#20252a 45%,#5d6a73 100%);clip-path:polygon(0 0,100% 0,100% 544px,0 600px);z-index:10}
.hero-photo{left:160px;top:30px;width:900px;height:520px;border-radius:40px;background:radial-gradient(ellipse at 50% 55%,#6ee03a 0%,#3fae22 45%,rgba(40,60,40,0) 75%)}
.hero-title{left:0;width:1200px;top:268px;text-align:center;color:var(--white);font-weight:900;font-size:58px;line-height:56px;text-transform:uppercase}
.btn-solid{background:var(--pink);color:var(--white);font-weight:700;font-size:14px;text-transform:uppercase;text-align:center}
.hero-btn{left:510px;top:413px;width:180px;height:46px;line-height:46px}

/* welcome */
.welcome{top:600px;height:500px;background:linear-gradient(120deg,#5fd0ec,#a2e4f4 60%,#7fd6ee);z-index:5}
.section-title{font-weight:900;font-size:27px;color:var(--navy);text-transform:uppercase}
.welcome .section-title{left:75px;top:132px}
.body-copy{font-size:14px;line-height:26px;color:var(--ink)}
.welcome .body-copy{left:75px;top:178px;width:630px}
.btn-outline{border:2px solid var(--pink);color:var(--pink);font-weight:700;font-size:13px;text-transform:uppercase;text-align:center;height:48px;line-height:44px;width:180px}
.welcome .btn-outline{left:75px;top:317px}
.welcome-car{left:810px;top:80px;width:350px;height:240px;border-radius:50%;background:radial-gradient(ellipse,#7be640 0%,#49b82b 45%,rgba(90,180,230,0) 72%)}

/* featured */
.featured{top:990px;height:640px;background:linear-gradient(135deg,#f4b8d8,#e78ac6 55%,#f3b4d6);clip-path:polygon(0 0,100% 60px,100% 100%,0 100%);z-index:6}
.featured .section-title{left:0;width:1200px;text-align:center;top:92px}
.card{top:155px;width:240px;height:323px;background:var(--white);box-shadow:0 2px 6px rgba(0,0,0,.12)}
.card-art{position:absolute;left:10px;top:30px;width:220px;height:95px;border-radius:40px;background:linear-gradient(90deg,#d8303f,#8a1020)}
.card-rule{position:absolute;left:0;right:0;top:178px;border-top:1px solid #e5e5e5}
.card-icon{position:absolute;left:99px;top:157px;width:42px;height:42px;border-radius:50%;background:var(--teal)}
.card-icon svg{position:absolute;left:12px;top:12px}
.card-price{position:absolute;left:0;right:0;top:214px;text-align:center;color:var(--pink);font-weight:900;font-size:18px}
.card-name{position:absolute;left:0;right:0;top:243px;text-align:center;color:var(--teal);font-weight:900;font-size:12.5px;text-transform:uppercase}
.card-text{position:absolute;left:20px;right:20px;top:262px;text-align:center;font-size:13px;line-height:19px}

/* new arrivals */
.arrivals{top:1553px;height:480px;background:linear-gradient(160deg,#e6da78,#dccd56 60%,#e4d370);clip-path:polygon(0 0,100% 46px,100% 100%,0 100%);z-index:7}
.arrivals-art{left:75px;top:122px;width:450px;height:204px;background:var(--white);box-shadow:0 1px 6px rgba(0,0,0,.15)}
.arrivals-art span{position:absolute;left:45px;top:30px;width:360px;height:140px;border-radius:60px;background:linear-gradient(90deg,#8c8c8c,#e0782a 50%,#8c8c8c)}
.arrivals .section-title{left:587px;top:114px}
.arrivals .body-copy{left:587px;top:160px;width:540px}
.arrivals .btn-outline{left:587px;top:297px}

/* reviews */
.reviews{top:1979px;height:620px;background:radial-gradient(ellipse at 50% 40%,#3ff0f6,#12d6e8 60%,#0fc6dd);clip-path:polygon(0 0,100% 42px,100% 100%,0 100%);z-index:8}
.reviews .section-title{left:0;width:1200px;text-align:center;top:105px}
.review{top:175px;width:500px;text-align:center}
.avatar{width:108px;height:108px;margin:0 auto;border-radius:50%;border:3px solid var(--white);background:linear-gradient(#b9c4cc,#6b7883)}
.review blockquote{font-style:italic;font-size:13.5px;line-height:25px;margin-top:22px;color:var(--ink)}
.review cite{display:block;font-style:normal;font-weight:900;font-size:13px;color:var(--pink);margin-top:10px;text-transform:uppercase}
.dots{left:0;width:1200px;top:464px;text-align:center;font-size:0}
.dots i{display:inline-block;width:10px;height:10px;border-radius:50%;background:var(--white);margin:0 4px}
.dots i.on{background:var(--navy)}

/* email */
.signup{top:2570px;height:300px;background:var(--white);clip-path:polygon(0 0,100% 20px,100% 100%,0 100%);z-index:9}
.signup .section-title{left:0;width:1200px;text-align:center;top:48px}
.signup .body-copy{left:0;width:1200px;text-align:center;top:92px}
.email-field{left:313px;top:139px;width:389px;height:48px;border:1px solid #bbb;font-size:14px;color:#888;line-height:46px;padding-left:48px}
.email-field svg{position:absolute;left:18px;top:17px}
.signup .btn-outline{left:711px;top:139px;width:179px}

/* footer */
.site-footer{top:2805px;height:386px;background:linear-gradient(180deg,#1c1d20,#0c0c0e);clip-path:polygon(0 0,100% 45px,100% 100%,0 100%);z-index:11}
.footer-col{top:98px}
.footer-col h4{font-size:14px;font-weight:900;color:#e8b22e;text-transform:uppercase;margin-bottom:8px}
.footer-col li{list-style:none;font-size:13.5px;line-height:28.5px;color:var(--white)}
.social{display:flex;gap:16px;margin-top:10px}
.social i{display:block;width:24px;height:24px;border-radius:50%;background:var(--white)}
.copyright{left:885px;top:220px;font-size:12.5px;line-height:22px;color:#9a9a9a}
</style>
</head>
<body>

<header class="band site-header">
  <div class="abs brand">Stickers<small>By Dwayne</small></div>
  <div class="abs topbar">
    <span class="phone"><svg width="14" height="14" viewBox="0 0 24 24"><path fill="#4fa83a" d="M6.6 10.8a15.1 15.1 0 0 0 6.6 6.6l2.2-2.2c.3-.3.7-.4 1-.2 1.1.4 2.3.6 3.6.6.6 0 1 .4 1 1V20c0 .6-.4 1-1 1C10.6 21 3 13.4 3 4c0-.6.4-1 1-1h3.5c.6 0 1 .4 1 1 0 1.3.2 2.5.6 3.6.1.3 0 .7-.2 1z"/></svg>1-800-555-0142</span>
    <span class="ship"><svg width="16" height="14" viewBox="0 0 24 20"><path fill="#1aa3b8" d="M0 2h15v11H0zM16 6h4l4 4v3h-8z"/><circle cx="5" cy="16" r="2.5" fill="#1aa3b8"/><circle cx="19" cy="16" r="2.5" fill="#1aa3b8"/></svg>Free Shipping on Order Over <b>$150</b></span>
    <svg width="14" height="14" viewBox="0 0 24 24"><circle cx="12" cy="7" r="5" fill="#777"/><path fill="#777" d="M2 23c0-6 4.5-9 10-9s10 3 10 9z"/></svg>
    <svg width="15" height="15" viewBox="0 0 24 24"><circle cx="10" cy="10" r="7" fill="none" stroke="#555" stroke-width="3"/><path d="M15 15l7 7" stroke="#555" stroke-width="3"/></svg>
    <span class="cart"><svg width="16" height="14" viewBox="0 0 24 20"><path fill="#1e3f9c" d="M0 0h4l1 3h19l-3 10H7L4 2H0z"/><circle cx="8" cy="17" r="2" fill="#1e3f9c"/><circle cx="20" cy="17" r="2" fill="#1e3f9c"/></svg>$0.00</span>
  </div>
  <nav class="abs main-nav">
    <a class="active" href="#">HOME</a><a href="#">ABOUT</a><a href="#">CAR DECALS</a><a href="#">NEW ARRIVALS</a><a href="#">SHOP</a><a href="#">BLOG</a><a href="#">REVIEWS</a><a href="#">CONTACT US</a>
  </nav>
</header>

<section class="band hero">
  <div class="abs hero-photo" role="img" aria-label="Photo of a green drift car with decals at a motorsport event"></div>
  <h1 class="abs hero-title">Welcome to<br>Stickers By Dwayne</h1>
  <div class="abs btn-solid hero-btn">View Decals</div>
</section>

<section class="band welcome">
  <h2 class="abs section-title">Welcome to our website</h2>
  <p class="abs body-copy">Aliquam molestie, mi et imperdiet euismod, dui purus auctor tellus, et interdum lacus lectus et ante. Sed accumsan sollicitudin sapien, sit amet adipiscing turpis gravida ac. In congue, neque ac lobortis volutpat, libero mauris varius mi, vitae suscipit ipsum ligula vitae risus. Duis aliquam nibh a dui iaculis viverra id a velit. Vivamus egestas risus in magna varius commodo. Sed semper viverra egestas.</p>
  <div class="abs btn-outline">Read More</div>
  <div class="abs welcome-car" role="img" aria-label="Illustration of a green sports car with a watercolour splash"></div>
</section>

<section class="band featured">
  <h2 class="abs section-title">Featured Decals</h2>
  <div class="abs card" style="left:75px">
    <div class="card-art" role="img" aria-label="Red and blue horse decal" style="background:linear-gradient(90deg,#c8283a,#2a3f9a)"></div>
    <div class="card-rule"></div>
    <div class="card-icon"><svg width="18" height="16" viewBox="0 0 24 20"><path fill="#fff" d="M0 0h4l1 3h19l-3 10H7L4 2H0z"/><circle cx="8" cy="17" r="2" fill="#fff"/><circle cx="20" cy="17" r="2" fill="#fff"/></svg></div>
    <div class="card-price">$0.00</div><div class="card-name">Vestibulum Ante</div><div class="card-text">Ipsum primis in faucibus orci luctus dui iaculis</div>
  </div>
  <div class="abs card" style="left:345px">
    <div class="card-art" role="img" aria-label="Red flame bird decal"></div>
    <div class="card-rule"></div>
    <div class="card-icon"><svg width="18" height="16" viewBox="0 0 24 20"><path fill="#fff" d="M0 0h4l1 3h19l-3 10H7L4 2H0z"/><circle cx="8" cy="17" r="2" fill="#fff"/><circle cx="20" cy="17" r="2" fill="#fff"/></svg></div>
    <div class="card-price">$0.00</div><div class="card-name">Vestibulum Ante</div><div class="card-text">Ipsum primis in faucibus orci luctus dui iaculis</div>
  </div>
  <div class="abs card" style="left:615px">
    <div class="card-art" role="img" aria-label="Black and red dragon decal with checkered flag" style="background:linear-gradient(90deg,#222,#b3202c,#222)"></div>
    <div class="card-rule"></div>
    <div class="card-icon"><svg width="18" height="16" viewBox="0 0 24 20"><path fill="#fff" d="M0 0h4l1 3h19l-3 10H7L4 2H0z"/><circle cx="8" cy="17" r="2" fill="#fff"/><circle cx="20" cy="17" r="2" fill="#fff"/></svg></div>
    <div class="card-price">$0.00</div><div class="card-name">Vestibulum Ante</div><div class="card-text">Ipsum primis in faucibus orci luctus dui iaculis</div>
  </div>
  <div class="abs card" style="left:885px">
    <div class="card-art" role="img" aria-label="Red swoosh decal" style="background:linear-gradient(90deg,#f03a5a,#c81838)"></div>
    <div class="card-rule"></div>
    <div class="card-icon"><svg width="18" height="16" viewBox="0 0 24 20"><path fill="#fff" d="M0 0h4l1 3h19l-3 10H7L4 2H0z"/><circle cx="8" cy="17" r="2" fill="#fff"/><circle cx="20" cy="17" r="2" fill="#fff"/></svg></div>
    <div class="card-price">$0.00</div><div class="card-name">Vestibulum Ante</div><div class="card-text">Ipsum primis in faucibus orci luctus dui iaculis</div>
  </div>
</section>

<section class="band arrivals">
  <div class="abs arrivals-art"><span role="img" aria-label="Checkered flag and wheel decal with orange lettering"></span></div>
  <h2 class="abs section-title">New Arrivals</h2>
  <p class="abs body-copy">Aliquam molestie, mi et imperdiet euismod, dui purus auctor tellus, et interdum lacus lectus et ante. Sed accumsan sollicitudin sapien, sit amet adipiscing turpis gravida ac. In congue, neque ac lobortis volutpat, libero mauris varius mi, vitae suscipit ipsum ligula vitae risus.</p>
  <div class="abs btn-outline">View All</div>
</section>

<section class="band reviews">
  <h2 class="abs section-title">Reviews</h2>
  <div class="abs review" style="left:142px">
    <div class="avatar" role="img" aria-label="Customer portrait"></div>
    <blockquote>" Aliquam molestie, mi et imperdiet euismod, dui purus auctor tellus, et interdum lacus lectus et ante. Sed accumsan sollicitudin sapien, sit amet adipiscing turpis gravida ac..."</blockquote>
    <cite>-Name Heading</cite>
  </div>
  <div class="abs review" style="left:678px">
    <div class="avatar" role="img" aria-label="Customer portrait"></div>
    <blockquote>" Aliquam molestie, mi et imperdiet euismod, dui purus auctor tellus, et interdum lacus lectus et ante. Sed accumsan sollicitudin sapien, sit amet adipiscing turpis gravida ac..."</blockquote>
    <cite>-Name Heading</cite>
  </div>
  <div class="abs dots"><i class="on"></i><i></i><i></i><i></i></div>
</section>

<section class="band signup">
  <h2 class="abs section-title">Email Sign Up</h2>
  <p class="abs body-copy">Aliquam molestie, mi et imperdiet euismod, dui purus auctor tellus, et interdum lacus lectus et ante</p>
  <div class="abs email-field"><svg width="16" height="12" viewBox="0 0 16 12"><rect x=".5" y=".5" width="15" height="11" fill="none" stroke="#999"/><path d="M.5.5l7.5 6 7.5-6" fill="none" stroke="#999"/></svg>Enter Email Address</div>
  <div class="abs btn-outline">Subscribe</div>
</section>

<footer class="band site-footer">
  <div class="abs footer-col" style="left:74px"><h4>Site Map</h4><ul><li>Home</li><li>About</li><li>Car Decals</li><li>New Arrivals</li><li>Shop</li><li>Blog</li><li>Reviews</li><li>Contact Us</li></ul></div>
  <div class="abs footer-col" style="left:345px"><h4>My Account</h4><ul><li>Log In</li><li>Register</li><li>Wishlist</li><li>My Account</li><li>Help</li></ul></div>
  <div class="abs footer-col" style="left:615px"><h4>Supports</h4><ul><li>Privacy Policy</li><li>Easy Return</li><li>Email Sign Up</li><li>Chat</li></ul></div>
  <div class="abs footer-col" style="left:885px"><h4>Follow Us</h4><div class="social"><i></i><i></i><i></i><i></i><i></i></div></div>
  <div class="abs copyright">Copyright © 2017. Company Name<br>All Right Reserved</div>
</footer>

</body>
</html>
```